Business Card Design Project

We have recently completed CraftHive projects for a new logo and wesbite.
We now require new business cards.
We hand out very little printed material to clients as all information is online. When we do hand out something, like a business card, we want it to have real impact and make a statement about the quality and professionalism of our company.
We have an idea of what we want our card to look like but we want a designer to make sure they have impact and look great.
Our requirements are…
Size: 85mm X 55mm - Landscape
Front of card: Logo plus the following contact information.
Dennis Marlow
Operations Manager
Phone +44(0) 1632 xxx xxx
Mobile +44(0) 7700 xxx xxx
Email denmo@korvantix.example
Address 17 Pellick Row, Aberdeen AB12 9QZ
Website www.korvantix.example
How you layout the front of the card is up to you, we would like to see some different ideas. Attached are two versions of our logo that may be used.
Back of card: We would like this to be simple but again have impact. Our current thought is to have the logo or just the large W design from the logo in white against a dark background, perhaps made up from the dark green in the logo.
The logos are attached so you can see the colours in them but the dark ones are..
Dark Blue = C:88, M:55, Y:44, K:28
Dark Green = C:87, M:53, Y:50, K:50
We sometimes also use a bright orange as an accent or highlight colour…
Orange: = C:0, M:39, Y:94, K:0

```html
<!DOCTYPE html>
<html lang="en">
<head>
<meta charset="utf-8">
<title>Korvantix Systems – Business Cards</title>
<link rel="stylesheet" href="https://fonts.googleapis.com/css2?family=Source+Sans+3:wght@400;600;700&display=swap">
<style>
  :root {
    --backdrop: #e8e5e1;
    --card-white: #ffffff;
    --deep-teal: #21424a;
    --teal-line: #7aa9ae;
    --soft-teal-text: #86b4b9;
    --olive: #7e8f5a;
    --ink: #21424a;
  }
  * { margin: 0; padding: 0; box-sizing: border-box; }
  html, body {
    width: 1200px; height: 800px; overflow: hidden;
    background: var(--backdrop);
    font-family: "Source Sans 3", "Helvetica Neue", Arial, sans-serif;
  }
  .sheet { position: relative; width: 1200px; height: 800px; }
  .card {
    position: absolute; width: 502px; height: 324px;
    border-radius: 16px; overflow: hidden;
    box-shadow: 0 3px 8px rgba(0,0,0,0.18);
  }
  .card--front { left: 88px; top: 72px; background: var(--card-white); }
  .card--back-dark { left: 610px; top: 68px; background: var(--deep-teal); }
  .card--back-gradient { left: 86px; top: 408px; background: linear-gradient(90deg, var(--deep-teal) 0%, #4d6b52 50%, var(--olive) 100%); }
  .card--back-white { left: 610px; top: 408px; background: var(--card-white); }

  /* Front card */
  .front-brand {
    position: absolute; left: 0; top: 0; width: 262px; height: 100%;
    display: flex; flex-direction: column; align-items: center; justify-content: center; gap: 10px;
    color: var(--ink);
  }
  .front-brand .mark {
    width: 22px; height: 22px; border-radius: 50%; background: var(--ink);
  }
  .front-brand .brand-name {
    font-weight: 700; font-size: 34px; letter-spacing: 1px; line-height: 1;
  }
  .front-brand .brand-sub {
    font-weight: 700; font-size: 17px; letter-spacing: 4px; line-height: 1;
  }
  .front-divider {
    position: absolute; left: 262px; top: 0; width: 5px; height: 100%; background: var(--teal-line);
  }
  .front-panel {
    position: absolute; left: 267px; top: 0; right: 0; height: 100%;
    background: var(--deep-teal); border-left: 1px solid var(--card-white);
    color: var(--soft-teal-text); padding: 64px 0 0 26px;
  }
  .person-name { font-weight: 600; font-size: 17px; letter-spacing: 0.3px; line-height: 1.1; }
  .person-role { font-size: 13px; margin-top: 4px; }
  .contact-list { list-style: none; margin-top: 25px; font-size: 13px; }
  .contact-list li { display: flex; align-items: center; gap: 5px; height: 19px; }
  .contact-list svg { width: 10px; height: 10px; fill: var(--soft-teal-text); flex: none; }
  .postal { margin-top: 16px; padding-left: 2px; font-size: 13px; font-style: normal; line-height: 19px; }

  /* Back cards */
  .back-content {
    position: absolute; inset: 0;
    display: flex; flex-direction: column; align-items: center;
  }
  .back-brand {
    margin-top: 104px; height: 90px;
    display: flex; align-items: center; gap: 16px;
    font-weight: 700; font-size: 58px; letter-spacing: 2px;
  }
  .back-brand .mark { width: 34px; height: 34px; }
  .back-url {
    margin-top: 78px; font-size: 15px; letter-spacing: 2.6px;
  }
  .card--back-dark .back-brand, .card--back-gradient .back-brand { color: #ffffff; }
  .card--back-dark .back-brand .mark, .card--back-gradient .back-brand .mark { background: #ffffff; }
  .card--back-dark .back-url, .card--back-gradient .back-url { color: #ffffff; }
  .card--back-white .back-brand { color: var(--ink); }
  .card--back-white .back-brand .mark { background: var(--ink); }
  .card--back-white .back-url { color: var(--ink); }
  .card--back-dark .back-brand { margin-top: 100px; }
  .card--back-dark .back-url { margin-top: 82px; }
</style>
</head>
<body>
<main class="sheet">

  <section class="card card--front" aria-label="Business card front">
    <div class="front-brand">
      <span class="mark"></span>
      <span class="brand-name">KORVANTIX</span>
      <span class="brand-sub">SYSTEMS</span>
    </div>
    <div class="front-divider"></div>
    <div class="front-panel">
      <p class="person-name">DENNIS MARLOW</p>
      <p class="person-role">Operations Manager</p>
      <ul class="contact-list">
        <li><svg viewBox="0 0 10 10" aria-hidden="true"><path d="M2 0.5 L3.8 2.6 L2.9 3.6 Q4 5.8 6.4 7.1 L7.4 6.2 L9.5 8 L8.3 9.5 Q4.5 9.3 1.6 6.4 Q-0.6 3.6 0.5 1.6 Z"/></svg>+44(0) 1632 xxx xxx</li>
        <li><svg viewBox="0 0 10 10" aria-hidden="true"><path d="M2.5 0 H7.5 V10 H2.5 Z M3.3 1 V7.6 H6.7 V1 Z M4.5 8.3 H5.5 V9.2 H4.5 Z"/></svg>+44(0) 7700 xxx xxx</li>
        <li><svg viewBox="0 0 10 10" aria-hidden="true"><path d="M0 2 H10 V9 H0 Z M0.8 2.6 L5 6 L9.2 2.6 Z"/></svg>denmo@korvantix.example</li>
        <li><svg viewBox="0 0 10 10" aria-hidden="true"><path d="M5 0 A5 5 0 1 0 5.01 0 Z M5 1 A4 4 0 0 1 5 9 A2 4 0 0 1 5 1 Z M1 4.5 H9 V5.5 H1 Z"/></svg>www.korvantix.example</li>
      </ul>
      <address class="postal">17 Pellick Row,<br>Aberdeen AB12 9QZ</address>
    </div>
  </section>

  <section class="card card--back-dark" aria-label="Business card back, dark">
    <div class="back-content">
      <div class="back-brand"><span class="mark"></span>KORVANTIX</div>
      <p class="back-url">www.korvantix.example</p>
    </div>
  </section>

  <section class="card card--back-gradient" aria-label="Business card back, gradient">
    <div class="back-content">
      <div class="back-brand"><span class="mark"></span>KORVANTIX</div>
      <p class="back-url">www.korvantix.example</p>
    </div>
  </section>

  <section class="card card--back-white" aria-label="Business card back, white">
    <div class="back-content">
      <div class="back-brand"><span class="mark"></span>KORVANTIX</div>
      <p class="back-url">www.korvantix.example</p>
    </div>
  </section>

</main>
</body>
</html>
```